National Intensive Course Provider needs an advert designed to appear in trams

We need an advertisement designed to put in trams, the dimensions are 660mm wide and 203mm height. We offer intensive driving courses all over the UK, allowing pupils to complete a full driving course within a week/two weeks with both the theory and practical tests included in the course (as required). We would like the colours used to be green and dark blue, maybe red also, whatever looks best from them colours really.

Key Points to highlight:
- Pass your driving test within 1 week
- Start your course as early as next week
- Both tests included as part of your course (if required)

I have attached some images which could be included in the design

```html
<!DOCTYPE html>
<html lang="en">
<head>
<meta charset="utf-8">
<title>Roadpace – Intensive Driving Courses Tram Advert</title>
<link rel="stylesheet" href="https://fonts.googleapis.com/css2?family=Open+Sans:wght@700;800&family=Roboto+Condensed:wght@700&display=swap">
<style>
  :root {
    --red: #e8121b;
    --navy: #07073a;
    --white: #ffffff;
    --cream: #f3e6b0;
    --ring: #8a8a8f;
    --photo-top: #5e8a3c;
    --photo-bottom: #b5261f;
  }
  * { margin: 0; padding: 0; box-sizing: border-box; }
  html, body {
    width: 1200px; height: 391px; overflow: hidden;
    background: var(--white);
  }
  .advert {
    position: relative; width: 1200px; height: 391px;
    font-family: "Open Sans", Arial, sans-serif;
    color: var(--white);
  }
  .advert__art { position: absolute; inset: 0; }
  .brand-name {
    position: absolute; left: 52px; top: 68px; width: 288px; height: 194px;
    display: flex; align-items: center; justify-content: center;
    font-weight: 800; font-size: 46px; letter-spacing: 1px;
    color: var(--white);
  }
  .start-badge {
    position: absolute; left: 448px; top: 62px; width: 160px;
    text-align: center; font-weight: 800; font-size: 25px; line-height: 32px;
  }
  .tests-note {
    position: absolute; right: 52px; top: 42px;
    text-align: right; font-weight: 800; font-size: 24px; line-height: 34px;
  }
  .headline {
    position: absolute; right: 64px; top: 188px;
    text-align: right;
    font-family: "Roboto Condensed", "Arial Narrow", sans-serif;
    font-weight: 700; font-size: 80px; line-height: 72px;
    letter-spacing: -0.5px;
  }
</style>
</head>
<body>
<main class="advert">
  <svg class="advert__art" width="1200" height="391" viewBox="0 0 1200 391" aria-hidden="false">
    <defs>
      <clipPath id="banner-clip"><rect x="18" y="24" width="1166" height="346"/></clipPath>
    </defs>
    <g class="banner" clip-path="url(#banner-clip)">
      <rect class="banner__base" x="18" y="24" width="1166" height="346" fill="var(--red)"/>
      <polygon class="banner__stripe" points="18,370 88,370 552,24 480,24" fill="var(--white)"/>
      <polygon class="banner__navy" points="104,370 1184,370 1184,112 872,180 560,24" fill="var(--navy)"/>
      <polyline class="banner__divider" points="556,26 872,182 1184,114" fill="none" stroke="var(--white)" stroke-width="5"/>

      <g class="photo-badge">
        <circle cx="424" cy="308" r="98" fill="var(--ring)"/>
        <circle cx="424" cy="308" r="93" fill="var(--cream)"/>
        <defs>
          <linearGradient id="photo-fill" x1="0" y1="0" x2="0" y2="1">
            <stop offset="0" stop-color="var(--photo-top)"/>
            <stop offset="1" stop-color="var(--photo-bottom)"/>
          </linearGradient>
        </defs>
        <circle role="img" aria-label="Photo of a happy pupil holding a driving test pass certificate beside a red car" cx="424" cy="308" r="89" fill="url(#photo-fill)"/>
      </g>
    </g>

    <rect class="brand-box" x="52" y="68" width="288" height="194" rx="34" fill="var(--navy)" stroke="var(--red)" stroke-width="4"/>

    <g class="start-badge__disc">
      <circle cx="528" cy="128" r="102" fill="var(--ring)"/>
      <circle cx="528" cy="128" r="96" fill="var(--cream)"/>
      <circle cx="528" cy="128" r="92" fill="var(--red)"/>
    </g>
  </svg>

  <div class="brand-name">Roadpace</div>

  <p class="start-badge">Start your course as early as next week</p>

  <p class="tests-note">Theory and practical tests included as<br>part of your course (if required)</p>

  <h1 class="headline">Pass Your Driving<br>Test Within 1 Week</h1>
</main>
</body>
</html>
```